Business card for Luxury Portable Restroom Trailer company

We are a Luxury Portable Restroom Trailer Company Called FALCRIDGE HIRES. Based in Orange County California. We provide portable restroom trailers for events, such as, Weddings, Concerts, Charity events, Sporting events, Tournaments, Corporate events, ect. We rent and Sell the Luxury restrooms. Our colors are white, grey, and Orange. As you will see in the logo we uploaded.
There are 2 people in the company so the names and titles will change for the 3 people but card will remain the same. Here is the information for each Person: Dwight Penner CFO 555 318-0476
next Person: Leon Marchetti VP 555 318-0476
Next Person: Owen Marchetti CEO 555 318-0476
Information to include on the card: Luxury Restroom Trailers Rental and Sales. Weddings, Concerts, Charity, Sporting and Corp. Events.

```html
<!DOCTYPE html>
<html lang="en">
<head>
<meta charset="UTF-8">
<title>Falcridge Hires – Business Card</title>
<link rel="stylesheet" href="https://fonts.googleapis.com/css2?family=Montserrat:wght@400;500;700;800&display=swap">
<style>
  :root {
    --orange: #f0722d;
    --grey: #5f5f61;
    --grey-light: #8a8a8c;
    --white: #ffffff;
    --ink: #1d1d1f;
    --backdrop: #e9e9eb;
  }
  * { box-sizing: border-box; margin: 0; padding: 0; }
  html, body {
    width: 1200px; height: 960px; overflow: hidden;
    background: var(--backdrop);
    font-family: "Montserrat", Arial, sans-serif;
  }
  .sheet {
    width: 1200px; height: 960px;
    display: flex; flex-direction: column; align-items: center; justify-content: center;
    gap: 60px;
  }
  .card {
    position: relative;
    width: 700px; height: 400px;
    border-radius: 22px;
    overflow: hidden;
    box-shadow: 0 8px 24px rgba(0,0,0,0.18);
  }

  /* Front face */
  .card--front {
    background: var(--orange);
    color: var(--white);
    display: flex; flex-direction: column; align-items: center; justify-content: center;
  }
  .brand-name {
    font-weight: 800;
    letter-spacing: 0.06em;
    line-height: 1;
    white-space: nowrap;
  }
  .card--front .brand-name { font-size: 58px; color: var(--white); }
  .services {
    margin-top: 56px;
    text-align: center;
    font-size: 17px;
    font-weight: 500;
    line-height: 1.6;
  }
  .services .dot {
    display: inline-block; width: 9px; height: 9px; border-radius: 50%;
    background: var(--white); margin: 0 8px 2px; vertical-align: middle;
  }

  /* Back face */
  .card--back { background: var(--white); }
  .card--back .swoosh { position: absolute; left: 0; bottom: 0; width: 700px; height: 400px; }
  .card--back .brand-name {
    position: absolute; right: 44px; top: 70px;
    font-size: 34px; color: var(--grey);
  }
  .team {
    position: absolute; left: 48px; top: 88px;
    display: flex; flex-direction: column; gap: 14px;
  }
  .member-name {
    color: var(--orange); font-weight: 800; font-size: 21px; letter-spacing: 0.02em;
    text-transform: uppercase;
  }
  .member-title { color: var(--ink); font-size: 15px; font-weight: 500; margin-top: 2px; }
  .member-phone {
    display: flex; align-items: center; gap: 8px;
    color: var(--ink); font-size: 15px; font-weight: 500; margin-top: 2px;
  }
  .member-phone svg { width: 15px; height: 15px; fill: var(--orange); }
</style>
</head>
<body>
<main class="sheet">

  <section class="card card--front" aria-label="Card front">
    <div class="brand-name">FALCRIDGE HIRES</div>
    <div class="services">
      <p><span class="dot"></span>Luxury Restroom Trailers Rental and Sales</p>
      <p><span class="dot"></span>Weddings <span class="dot"></span>Concerts <span class="dot"></span>Charity <span class="dot"></span>Sporting and Corp <span class="dot"></span>Events</p>
    </div>
  </section>

  <section class="card card--back" aria-label="Card back">
    <svg class="swoosh" viewBox="0 0 700 400" preserveAspectRatio="none" aria-hidden="true">
      <path d="M0 400 L0 350 Q340 330 700 170 L700 400 Z" fill="var(--orange)"/>
      <path d="M170 338 Q430 300 700 150 L700 160 Q430 310 170 338 Z" fill="var(--grey)"/>
    </svg>

    <div class="brand-name">FALCRIDGE HIRES</div>

    <div class="team">
      <div class="member">
        <div class="member-name">Dwight Penner</div>
        <div class="member-title">CFO</div>
        <div class="member-phone">
          <svg viewBox="0 0 24 24"><path d="M6.6 10.8a15.1 15.1 0 0 0 6.6 6.6l2.2-2.2a1 1 0 0 1 1-.25 11.4 11.4 0 0 0 3.6.57 1 1 0 0 1 1 1V20a1 1 0 0 1-1 1A17 17 0 0 1 3 4a1 1 0 0 1 1-1h3.5a1 1 0 0 1 1 1c0 1.25.2 2.45.57 3.6a1 1 0 0 1-.25 1z"/></svg>
          555 318-0476
        </div>
      </div>
      <div class="member">
        <div class="member-name">Leon Marchetti</div>
        <div class="member-title">VP</div>
        <div class="member-phone">
          <svg viewBox="0 0 24 24"><path d="M6.6 10.8a15.1 15.1 0 0 0 6.6 6.6l2.2-2.2a1 1 0 0 1 1-.25 11.4 11.4 0 0 0 3.6.57 1 1 0 0 1 1 1V20a1 1 0 0 1-1 1A17 17 0 0 1 3 4a1 1 0 0 1 1-1h3.5a1 1 0 0 1 1 1c0 1.25.2 2.45.57 3.6a1 1 0 0 1-.25 1z"/></svg>
          555 318-0476
        </div>
      </div>
      <div class="member">
        <div class="member-name">Owen Marchetti</div>
        <div class="member-title">CEO</div>
        <div class="member-phone">
          <svg viewBox="0 0 24 24"><path d="M6.6 10.8a15.1 15.1 0 0 0 6.6 6.6l2.2-2.2a1 1 0 0 1 1-.25 11.4 11.4 0 0 0 3.6.57 1 1 0 0 1 1 1V20a1 1 0 0 1-1 1A17 17 0 0 1 3 4a1 1 0 0 1 1-1h3.5a1 1 0 0 1 1 1c0 1.25.2 2.45.57 3.6a1 1 0 0 1-.25 1z"/></svg>
          555 318-0476
        </div>
      </div>
    </div>
  </section>

</main>
</body>
</html>
```